Business Card for beauty technology startup

Design Glimora Business Card for a Beauty, based on the website identity and colors (https://www.glimora-example.com).
Glimora is a beauty tech startup that gathers helpful product info for beauty lovers and consumers (such as availability on stores, price range and product reviews) for makeup products. The card design must be young, colorful but clean, and very modern.

Target Market(s)

woman, 15-35

Industry/Entity Type

Cosmetics

Contact Information for Business Card

Full Name, address, phone

Font styles to use
Other font styles liked:
• Advent Pro

Colors
e34297
86cfc6
ffffff
5c5c5c
e8e8e8
e667a6
b2b2b2

Requirements
Must have
• One full colored side with a creative design and another with card info
• Use Color palette: #95C5C5 and/or #D38AA5
• Use fonts: Advent Pro
• Use website identity: https://www.glimora-example.com
Nice to have
• If needed extra font: Roboto

```html
<!DOCTYPE html>
<html lang="en">
<head>
<meta charset="utf-8">
<title>Glimora Business Card</title>
<link rel="stylesheet" href="https://fonts.googleapis.com/css2?family=Advent+Pro:wght@400;500;600&family=Roboto:wght@400&display=swap">
<style>
  :root {
    --backdrop: #3b3b3d;
    --card: #232326;
    --rose: #b57c98;
    --teal: #78a7a8;
    --teal-light: #95c5c5;
    --ink-dark: #26262a;
    --faint: #2c2c30;
    --gloss: #3a3a3f;
  }
  * { margin: 0; padding: 0; box-sizing: border-box; }
  html, body { width: 799px; height: 1200px; overflow: hidden; }
  body { background: var(--backdrop); position: relative; font-family: "Roboto", sans-serif; }

  .card {
    position: absolute;
    left: 80px;
    width: 640px;
    height: 366px;
    background: var(--card);
    border-radius: 4px;
    box-shadow: 0 14px 30px rgba(0,0,0,0.45);
    overflow: hidden;
  }
  .card--front { top: 150px; }
  .card--back { top: 684px; }

  /* Front */
  .front-mark {
    position: absolute; inset: 0;
    display: flex; align-items: center; justify-content: center; gap: 18px;
  }
  .front-mark__dot {
    width: 22px; height: 22px; border-radius: 50%;
    background: var(--gloss);
  }
  .front-mark__name {
    font-family: "Advent Pro", sans-serif;
    font-weight: 500;
    font-size: 58px;
    letter-spacing: 10px;
    color: var(--gloss);
  }

  /* Back */
  .back-decor { position: absolute; left: 340px; top: 70px; }
  .brand {
    position: absolute; left: 40px; top: 34px;
    display: flex; align-items: center; gap: 16px;
  }
  .brand__dot {
    width: 40px; height: 40px; border-radius: 50%;
    border: 2px solid var(--rose);
  }
  .brand__name {
    font-family: "Advent Pro", sans-serif;
    font-weight: 400; font-size: 44px; letter-spacing: 9px;
    color: var(--rose);
  }
  .holder {
    position: absolute; left: 40px; top: 146px;
    font-family: "Advent Pro", sans-serif;
    font-weight: 600; font-size: 25px; letter-spacing: 1px;
    color: var(--teal-light);
  }
  .bands { position: absolute; left: 0; top: 0; }
  .contact {
    position: absolute; left: 372px; top: 190px;
    font-size: 15px; line-height: 19px; color: var(--rose);
    list-style: none;
  }
  .contact li { display: flex; align-items: center; gap: 10px; }
  .contact .address { padding-left: 24px; margin-bottom: 2px; }
  .contact svg { flex: none; }
  .website {
    position: absolute; left: 250px; top: 318px; width: 390px;
    text-align: center; font-size: 15px; color: var(--ink-dark);
  }
</style>
</head>
<body>
  <section class="card card--front" aria-label="Card front">
    <div class="front-mark">
      <span class="front-mark__dot"></span>
      <span class="front-mark__name">GLIMORA</span>
    </div>
  </section>

  <section class="card card--back" aria-label="Card back">
    <svg class="back-decor" width="260" height="260" viewBox="0 0 260 260" aria-hidden="true">
      <circle cx="130" cy="130" r="120" fill="none" stroke="var(--faint)" stroke-width="6"/>
    </svg>

    <svg class="bands" width="640" height="366" viewBox="0 0 640 366" aria-hidden="true">
      <rect x="0" y="290" width="290" height="24" fill="var(--rose)"/>
      <polygon points="255,314 288,284 640,284 640,366 255,366" fill="var(--teal)"/>
    </svg>

    <div class="brand">
      <span class="brand__dot"></span>
      <span class="brand__name">GLIMORA</span>
    </div>

    <div class="holder">MAYA LINDEN</div>

    <ul class="contact">
      <li class="address">27 Orchard Row, Fairview Town,<br>Country - 540210</li>
      <li>
        <svg width="14" height="14" viewBox="0 0 24 24" aria-hidden="true"><path d="M6.6 10.8a15 15 0 0 0 6.6 6.6l2.2-2.2a1 1 0 0 1 1-.25 11.4 11.4 0 0 0 3.6.57 1 1 0 0 1 1 1V20a1 1 0 0 1-1 1A17 17 0 0 1 3 4a1 1 0 0 1 1-1h3.5a1 1 0 0 1 1 1c0 1.25.2 2.45.57 3.6a1 1 0 0 1-.25 1z" fill="var(--rose)"/></svg>
        00 555 010 246
      </li>
      <li>
        <svg width="14" height="12" viewBox="0 0 24 18" aria-hidden="true"><rect x="1" y="1" width="22" height="16" fill="none" stroke="var(--rose)" stroke-width="2"/><path d="M1 1l11 9 11-9" fill="none" stroke="var(--rose)" stroke-width="2"/></svg>
        hello@glimora-example.com
      </li>
    </ul>

    <div class="website">www.glimora-example.com</div>
  </section>
</body>
</html>
```